Business Card Design

Business Card for professional consulting firm working with large financial institutions.

Target Market(s)

Executive buyers

Industry/Entity Type

Banking

Contact Information for Business Card

Mild creativity wanted. Not boring, but do elaborate artwork.

Font styles to use
Serif
Sans Serif

Colors

Designer to choose colors to be used in the design.

Requirements
Must have
• Standard business card features - company name, individual name, telephone, website, email, locations.
Nice to have
• Two colors
Should not have
• too many colors, fancy printing, cartoons.

```html
<!DOCTYPE html>
<html lang="en">
<head>
<meta charset="utf-8">
<title>Valecrest Business Card</title>
<link href="https://fonts.googleapis.com/css2?family=Roboto:wght@400;500&family=Roboto+Condensed:wght@700&display=swap" rel="stylesheet">
<style>
  :root {
    --backdrop: #e8e4de;
    --card-front: #f4f4f4;
    --card-back: #c2c2c2;
    --ink: #111111;
    --ink-soft: #555555;
    --ink-muted: #a6a6a6;
    --accent-bar: #b8b8b8;
    --paper-white: #ffffff;
  }
  * { margin: 0; padding: 0; box-sizing: border-box; }
  html, body {
    width: 1200px;
    height: 960px;
    overflow: hidden;
    background: var(--backdrop);
    font-family: "Roboto", Arial, sans-serif;
  }
  .card {
    position: absolute;
    box-shadow: 0 3px 6px rgba(0,0,0,0.35);
  }
  .card-front {
    left: 314px; top: 113px;
    width: 600px; height: 343px;
    background: var(--card-front);
  }
  .holder {
    position: absolute;
    right: 31px; top: 33px;
    text-align: right;
  }
  .holder-name {
    font-family: "Roboto Condensed", Arial, sans-serif;
    font-weight: 700;
    font-size: 23px;
    color: var(--ink);
    line-height: 26px;
  }
  .holder-role {
    font-family: "Roboto Condensed", Arial, sans-serif;
    font-weight: 700;
    font-size: 15px;
    color: var(--ink-muted);
    line-height: 18px;
  }
  .holder-bar {
    position: absolute;
    right: 0; top: 28px;
    width: 12px; height: 49px;
    background: var(--ink);
  }
  .wordmark {
    position: absolute;
    left: 0; right: 0;
    text-align: center;
    font-weight: 400;
  }
  .card-front .wordmark {
    top: 117px;
    font-size: 31px;
    color: #333333;
  }
  .contact-bar {
    position: absolute;
    left: 0; top: 205px;
    width: 10px; height: 108px;
    background: var(--accent-bar);
  }
  .contact {
    position: absolute;
    left: 27px; top: 209px;
    font-size: 14px;
    color: var(--ink-soft);
    line-height: 18px;
    list-style: none;
  }
  .contact-address { margin-bottom: 4px; }
  .contact-line { display: flex; align-items: center; height: 19.5px; }
  .contact-line svg { width: 12px; height: 12px; margin-right: 9px; fill: var(--ink); }
  .card-back {
    left: 312px; top: 472px;
    width: 599px; height: 343px;
    background: var(--card-back);
  }
  .card-back .wordmark {
    top: 145px;
    font-size: 36px;
    color: var(--paper-white);
  }
  .web-band {
    position: absolute;
    left: 0; top: 275px;
    width: 100%; height: 29px;
    background: var(--ink);
    color: var(--paper-white);
    font-size: 14px;
    letter-spacing: 5.5px;
    text-align: center;
    line-height: 29px;
  }
</style>
</head>
<body>
  <section class="card card-front">
    <div class="holder">
      <div class="holder-name">DANIEL REYES</div>
      <div class="holder-role">CEO/FOUNDER</div>
    </div>
    <div class="holder-bar"></div>
    <div class="wordmark">valecrest</div>
    <div class="contact-bar"></div>
    <ul class="contact">
      <li class="contact-address">valecrest&nbsp; 2140 Harbor View Road<br>Fairbanks, Alaska 99701</li>
      <li class="contact-line">
        <svg viewBox="0 0 24 24" aria-hidden="true"><path d="M6.6 10.8a15.1 15.1 0 0 0 6.6 6.6l2.2-2.2c.3-.3.7-.4 1-.2 1.1.4 2.3.6 3.6.6.6 0 1 .4 1 1V20c0 .6-.4 1-1 1A17 17 0 0 1 3 4c0-.6.4-1 1-1h3.5c.6 0 1 .4 1 1 0 1.3.2 2.5.6 3.6.1.3 0 .7-.2 1z"/></svg>
        907 555 0148
      </li>
      <li class="contact-line">
        <svg viewBox="0 0 24 24" aria-hidden="true"><path d="M2 5h20v14H2z M2 5l10 7 10-7" fill="none" stroke="#111" stroke-width="0"/><path d="M2 5h20v2l-10 7L2 7z"/><path d="M2 9l10 7 10-7v10H2z"/></svg>
        info@valecrest.com
      </li>
      <li class="contact-line">
        <svg viewBox="0 0 24 24" aria-hidden="true"><circle cx="12" cy="12" r="10"/><path d="M7 6c2 1 3 3 2 5s1 3 3 3 1 4-1 5M15 4c-1 2 0 3 2 3s3 2 2 4" fill="none" stroke="#f4f4f4" stroke-width="2"/></svg>
        www.valecrest.com
      </li>
    </ul>
  </section>

  <section class="card card-back">
    <div class="wordmark">valecrest</div>
    <div class="web-band">www.valecrest.com</div>
  </section>
</body>
</html>
```